Corvin Ridge Software PowerPoint template

We are a software company selling endpoint visibility, access and security technology to enterprise-level IT departments.
Our technology helps organizations gain comprehensive visibility into and control over devices accessing their corporate network so they can quickly identify and address suspicious activity on the network that could lead to potential threats like data breaches.
This technology can cost organizations upwards of $1M - depending on the size of the organization. Our primary clients are Vestral 2,000 companies.
We want a professional, polished PowerPoint template that we can use for all company presentations. Please include:
Title page
Section page
General info page
Thank you page
Logo options and color specs are attached.
Please include our tagline on at least the title page: Discover the edge. Optimize the whole.
Reason: Seeking more options. Looking for a clean design that uses lots of white space.
Software

```html
<!DOCTYPE html>
<html lang="en">
<head>
<meta charset="utf-8">
<title>Information Graphics – Corvin Ridge Software</title>
<link rel="stylesheet" href="https://fonts.googleapis.com/css2?family=Catamaran:wght@500;600&family=Carlito:wght@400;700&display=swap">
<style>
  :root {
    --brand-red: #8e1b1f;
    --brand-copper: #d4825e;
    --ink: #111111;
    --slate: #555555;
    --mist: #d6d6d6;
    --ring: #bdbdbd;
    --rule: #bfbfbf;
    --paper: #ffffff;
  }
  * { margin: 0; padding: 0; box-sizing: border-box; }
  html, body { width: 1200px; height: 849px; overflow: hidden; background: var(--paper); }
  .slide {
    position: relative;
    width: 1200px;
    height: 849px;
    overflow: hidden;
    background: var(--paper);
    font-family: "Carlito", "Calibri", Arial, sans-serif;
    color: var(--ink);
  }
  .header-accent {
    position: absolute; left: 135px; top: 0;
    width: 6px; height: 86px; background: var(--brand-red);
  }
  .deck-heading {
    position: absolute; left: 154px; top: 37px;
    font-family: "Catamaran", "Carlito", sans-serif;
    font-weight: 500; font-size: 21px; letter-spacing: 0.2px;
    color: var(--brand-red); line-height: 1;
  }
  .deck-date {
    position: absolute; left: 154px; top: 62px;
    font-family: "Catamaran", "Carlito", sans-serif;
    font-weight: 500; font-size: 19px; color: var(--ink); line-height: 1;
  }
  .deck-date strong { font-weight: 600; }
  .pattern-area {
    position: absolute; left: 800px; top: 0;
    width: 400px; height: 370px;
    background: radial-gradient(ellipse at 70% 35%, #efefef 0%, #f6f6f6 45%, rgba(255,255,255,0) 75%);
  }
  .page-badge {
    position: absolute; left: 1098px; top: 36px;
    width: 56px; height: 56px; border-radius: 50%;
    background: var(--brand-copper);
    display: flex; align-items: center; justify-content: center;
    font-family: "Carlito", sans-serif; font-weight: 700; font-size: 17px;
    color: var(--paper);
  }
  .slide-title {
    position: absolute; left: 126px; top: 166px;
    font-family: "Catamaran", "Carlito", sans-serif;
    font-weight: 600; font-size: 70px; line-height: 1;
    color: var(--brand-copper); letter-spacing: -0.5px;
  }
  .hub-diagram { position: absolute; left: 0; top: 0; }
  .info-list {
    position: absolute; left: 626px; top: 285px; width: 420px;
    list-style: none;
  }
  .info-item {
    font-size: 16px; line-height: 24px; color: var(--ink);
    height: 114px; white-space: nowrap;
  }
  .info-item:nth-child(3) { height: 107px; }
  .footer-rule {
    position: absolute; left: 128px; top: 769px;
    width: 706px; height: 1px; background: var(--rule);
  }
  .copyright {
    position: absolute; left: 132px; top: 779px;
    font-size: 12px; color: #333333;
  }
  .brand-lockup {
    position: absolute; left: 858px; top: 740px;
    display: flex; align-items: center; gap: 14px;
  }
  .brand-mark {
    width: 50px; height: 50px; border-radius: 50%;
    background: var(--brand-copper);
  }
  .brand-name {
    font-family: "Catamaran", "Carlito", sans-serif;
    font-weight: 600; font-size: 25px; line-height: 28px;
    letter-spacing: 3px; color: var(--brand-red);
  }
</style>
</head>
<body>
<main class="slide">
  <div class="header-accent"></div>
  <p class="deck-heading">PPT HEADING GOES HERE</p>
  <p class="deck-date">FEB, <strong>2015</strong></p>

  <div class="pattern-area" role="img" aria-label="Decorative pattern of light grey outlined circles"></div>
  <p class="page-badge">01</p>

  <h1 class="slide-title">Information Graphics</h1>

  <svg class="hub-diagram" width="1200" height="849" viewBox="0 0 1200 849">
    <defs>
      <symbol id="icon-scale" viewBox="0 0 40 40">
        <g fill="none" stroke="currentColor" stroke-width="2" stroke-linecap="round">
          <path d="M20 7 V33 M8 11 H32 M13 34 H27"/>
          <path d="M8 11 L4 22 M8 11 L12 22 M32 11 L28 22 M32 11 L36 22"/>
        </g>
        <g fill="currentColor">
          <circle cx="20" cy="6" r="2.2"/>
          <path d="M3 22 Q8 28 13 22 Z M27 22 Q32 28 37 22 Z"/>
          <path d="M16 34 Q20 29 24 34 Z"/>
        </g>
      </symbol>
      <symbol id="icon-pool" viewBox="0 0 40 40">
        <g fill="none" stroke="currentColor" stroke-width="2.4" stroke-linecap="round">
          <path d="M14 20 V7 Q14 4 17 4 M24 20 V7 Q24 4 27 4"/>
          <path d="M14 10 H24 M14 15 H24"/>
          <path d="M4 24 q4 -3 8 0 t8 0 t8 0 t8 0"/>
          <path d="M4 29 q4 -3 8 0 t8 0 t8 0 t8 0"/>
          <path d="M4 34 q4 -3 8 0 t8 0 t8 0 t8 0"/>
        </g>
      </symbol>
      <symbol id="icon-network" viewBox="0 0 40 40">
        <g fill="none" stroke="currentColor" stroke-width="1.8">
          <path d="M20 15 V21 M12 29 H28"/>
          <ellipse cx="9" cy="31" rx="5" ry="2"/>
          <ellipse cx="31" cy="31" rx="5" ry="2"/>
          <ellipse cx="20" cy="22" rx="5" ry="2"/>
        </g>
        <g fill="currentColor">
          <circle cx="20" cy="10" r="4"/>
          <rect x="17" y="14" width="6" height="6" rx="1"/>
          <circle cx="9" cy="19" r="4"/>
          <rect x="6" y="23" width="6" height="6" rx="1"/>
          <circle cx="31" cy="19" r="4"/>
          <rect x="28" y="23" width="6" height="6" rx="1"/>
        </g>
      </symbol>
    </defs>
    <g stroke="#9a9a9a" stroke-width="1.2" stroke-dasharray="2 3" fill="none">
      <line x1="348" y1="513" x2="228" y2="399"/>
      <line x1="348" y1="513" x2="428" y2="345"/>
      <line x1="348" y1="513" x2="542" y2="428"/>
      <line x1="348" y1="513" x2="197" y2="598"/>
      <line x1="348" y1="513" x2="513" y2="606"/>
    </g>
    <g fill="var(--paper)" stroke="var(--ring)" stroke-width="1.5">
      <circle cx="228" cy="399" r="55"/>
      <circle cx="428" cy="345" r="47"/>
      <circle cx="348" cy="513" r="74"/>
    </g>
    <circle cx="228" cy="399" r="47" fill="var(--brand-red)"/>
    <circle cx="428" cy="345" r="40" fill="var(--slate)"/>
    <circle cx="348" cy="513" r="64" fill="var(--brand-copper)"/>
    <g fill="var(--paper)" stroke="var(--mist)" stroke-width="7">
      <circle cx="542" cy="428" r="43"/>
      <circle cx="197" cy="598" r="48"/>
      <circle cx="513" cy="606" r="59"/>
    </g>
    <g style="color: var(--paper)">
      <use href="#icon-pool" x="202" y="373" width="52" height="52"/>
      <use href="#icon-scale" x="405" y="322" width="46" height="46"/>
      <use href="#icon-network" x="311" y="476" width="74" height="74"/>
    </g>
    <g style="color: #cfcfcf">
      <use href="#icon-scale" x="519" y="405" width="46" height="46"/>
      <use href="#icon-scale" x="172" y="573" width="50" height="50"/>
      <use href="#icon-pool" x="483" y="576" width="60" height="60"/>
    </g>
  </svg>

  <ul class="info-list">
    <li class="info-item">Our technology helps organizations gain<br>comprehensive visibility into and control over<br>devices accessing their corporate network so they</li>
    <li class="info-item">Our technology helps organizations gain<br>comprehensive visibility into and control over<br>devices accessing their corporate network so they</li>
    <li class="info-item">Our technology helps organizations gain<br>comprehensive visibility into and control over<br>devices accessing their corporate network so they</li>
    <li class="info-item">Our technology helps organizations gain<br>comprehensive visibility into and control over</li>
  </ul>

  <div class="footer-rule"></div>
  <p class="copyright">©2015 Corvin Ridge Software</p>

  <div class="brand-lockup">
    <span class="brand-mark" aria-hidden="true"></span>
    <p class="brand-name">CORVIN RIDGE<br>SOFTWARE</p>
  </div>
</main>
</body>
</html>
```